Copper&Finch Brewery.... beer posters 6 posters

Copper and Finch Brewery sits on the Black river in Port Huron MI. (418 Lark ST) We are 1/4 mile from the St Clair River and 1 mile from Lake Huron(one of the great lakes) In the spring-summer-fall we have lots of boat traffic coming to our docks to dock and come in for our cold beer and wings! I would like posters of each beer style we are brewing, currently there are 6. see banner picture attached. I am looking for a poster of each beer that would provoke excitement and interest in both the Copper & Finch Brand and the beer on the poster. I am wide open on style of poster. The attachments are there to be used if you see a fit. (primarily to help you get to know the place). The medallion is our primary branding logo. The shimmering night water of the brewery back picture could make a cool backdrop or a cut portion/ or not. The banner picture has all the beer types and names. I would like a poster for each beer...I could be sold a poster with two or three beers if it didn't lose the individual beers.

Lantern Fox
Tart crisp taste
mild flavor
not to strong
recommend for people who want beer with a light flavor
mild
bitter with lite body and good finish with no after taste

Gentle Meadow
smooth clean taste
lite taste
clean and light
light flavor sweet kick at the end
lite body
very comparable to domestic

Brown
nice brown color
aroma of caramel and chocolate
not to heavy
strong bold taste
tart strong flavor
strong, super light and airy

Stout
nice stout
clean flavor
not to heavy
notes of a cinnamon oatmeal flavor
tart and bitter
aromatic, creamy finish and nice and heavy
hints of cocoa

Wild Maple
clean and fruity with hints of Banana and citrus
notes of Banana
clean crisp taste
light/medium flavor
tart yet sweet
aromatic with hint of Banana

Old Owl
a nice hopy IPA with hints of citrus and earthy notes
strong citrus taste
piney and very earthy
Tart and heavy

Target Market(s)

Beer Drinkers entering my brewery. Community as i post posters

Font styles to use
Other font styles liked:
• see material uploaded, use font on medallion for brewery. open on rest of poster

Colors

Designer to choose colors to be used in the design.

Requirements
Must have
• brand awareness, very cool vibe. colorful.
• Beers below listed as shown in new pictures( darkest to lightest color)
• they are all big beers ranging from 6.2 - 7.2 ABV. full of flavor. the ways beers should be brewed
• Pine Hollow Ember Oatmeal Stout
• Brown
• Old Owl IPA
• Lantern Fox ...English Pale Ale
• Wild Maple
• Gentle Meadow....Pale Ale
• I have been asked to put up more info on beers we make....
Nice to have
• almost like a movie release poster
• Multiple beers on one poster
Should not have
• plain white poster

```html
<!DOCTYPE html>
<html lang="en">
<head>
<meta charset="utf-8">
<title>Copper &amp; Finch Brewery – Pine Hollow Ember Oatmeal Stout</title>
<link rel="stylesheet" href="https://fonts.googleapis.com/css2?family=Righteous&family=Jost:ital,wght@0,300;0,400;0,700;1,600&display=swap">
<style>
  :root {
    --navy: #0e1a36;
    --navy-deep: #08112a;
    --ember: #f2500f;
    --ember-dark: #b8280a;
    --sky-cyan: #2fc8f4;
    --cyan-deep: #129fe0;
    --pale: #e9f6e6;
    --title-grey: #d4d4d4;
    --tag-copper: #c57a1f;
    --note-orange: #f28a00;
    --ink: #0a0a0a;
    --wine: #9b1313;
    --paper: #ffffff;
  }
  html, body {
    margin: 0;
    padding: 0;
    width: 950px;
    height: 1200px;
    overflow: hidden;
    background: var(--navy-deep);
  }
  .poster {
    position: relative;
    width: 950px;
    height: 1200px;
    overflow: hidden;
    font-family: "Jost", "Century Gothic", sans-serif;
  }
  .backdrop {
    position: absolute;
    inset: 0;
  }
  .headline {
    position: absolute;
    left: 0;
    top: 0;
    width: 950px;
    height: 140px;
  }
  .tagline {
    position: absolute;
    left: 76px;
    top: 150px;
    margin: 0;
    font-weight: 300;
    font-size: 48px;
    line-height: 1;
    color: var(--tag-copper);
    letter-spacing: 0.5px;
  }
  .tasting-notes {
    position: absolute;
    right: 455px;
    top: 388px;
    margin: 0;
    padding: 0;
    list-style: none;
    text-align: right;
    font-weight: 600;
    font-style: italic;
    font-size: 24px;
    line-height: 39px;
    color: var(--note-orange);
    white-space: nowrap;
  }
  .beer-name {
    position: absolute;
    left: 0;
    top: 835px;
    width: 950px;
    height: 90px;
  }
  .beer-style {
    position: absolute;
    left: 0;
    width: 918px;
    top: 932px;
    margin: 0;
    text-align: center;
    font-weight: 400;
    font-size: 56px;
    line-height: 1;
    color: var(--ink);
  }
  .invite {
    position: absolute;
    left: 0;
    width: 918px;
    text-align: center;
    margin: 0;
    color: var(--wine);
    font-weight: 400;
    line-height: 1;
  }
  .invite-lead { top: 1027px; font-size: 29px; }
  .invite-main { top: 1061px; font-size: 41px; }
  .address {
    position: absolute;
    left: 0;
    width: 918px;
    top: 1112px;
    margin: 0;
    text-align: center;
    font-weight: 700;
    font-size: 45px;
    line-height: 1;
    color: var(--ink);
  }
  .brand-seal {
    position: absolute;
    left: 628px;
    top: 525px;
    width: 294px;
    height: 294px;
    border-radius: 50%;
    background: var(--paper);
    display: flex;
    align-items: center;
    justify-content: center;
    text-align: center;
  }
  .brand-seal-name {
    font-family: "Righteous", "Jost", sans-serif;
    font-size: 36px;
    line-height: 1.1;
    color: var(--ink);
  }
</style>
</head>
<body>
<main class="poster">

  <svg class="backdrop" width="950" height="1200" viewBox="0 0 950 1200" xmlns="http://www.w3.org/2000/svg">
    <defs>
      <linearGradient id="river-night" x1="0" y1="0" x2="0" y2="1">
        <stop offset="0" stop-color="#0f1d3d"/>
        <stop offset="0.4" stop-color="#17263c"/>
        <stop offset="0.62" stop-color="#233126"/>
        <stop offset="0.8" stop-color="#1a2838"/>
        <stop offset="1" stop-color="#0e1a30"/>
      </linearGradient>
      <radialGradient id="tree-glow" cx="0.55" cy="0.5" r="0.5">
        <stop offset="0" stop-color="#3a4a22" stop-opacity="0.75"/>
        <stop offset="1" stop-color="#3a4a22" stop-opacity="0"/>
      </radialGradient>
      <radialGradient id="water-shimmer" cx="0.5" cy="0.5" r="0.5">
        <stop offset="0" stop-color="#5a4a2a" stop-opacity="0.55"/>
        <stop offset="1" stop-color="#5a4a2a" stop-opacity="0"/>
      </radialGradient>
      <linearGradient id="ember-right" x1="0" y1="0" x2="1" y2="0">
        <stop offset="0" stop-color="#f2500f" stop-opacity="0"/>
        <stop offset="0.45" stop-color="#e8420c" stop-opacity="0.8"/>
        <stop offset="1" stop-color="#f25a14"/>
      </linearGradient>
      <linearGradient id="ember-left" x1="0" y1="0" x2="1" y2="0">
        <stop offset="0" stop-color="#f05a12"/>
        <stop offset="1" stop-color="#c8300a"/>
      </linearGradient>
      <linearGradient id="lagoon" x1="0" y1="0" x2="1" y2="0">
        <stop offset="0" stop-color="#1590e0"/>
        <stop offset="0.15" stop-color="#2fc8f4"/>
        <stop offset="1" stop-color="#34c6f2"/>
      </linearGradient>
      <linearGradient id="taproom-glow" x1="0" y1="0" x2="1" y2="1">
        <stop offset="0" stop-color="#5aa9c8" stop-opacity="0"/>
        <stop offset="0.5" stop-color="#6f9fb8" stop-opacity="0.7"/>
        <stop offset="1" stop-color="#e7d545" stop-opacity="0.85"/>
      </linearGradient>
      <linearGradient id="pint-tones" x1="0" y1="0" x2="0" y2="1">
        <stop offset="0" stop-color="#5a4c40"/>
        <stop offset="0.3" stop-color="#1e1817"/>
        <stop offset="0.85" stop-color="#171112"/>
        <stop offset="1" stop-color="#3a2622"/>
      </linearGradient>
    </defs>

    <!-- night river scene -->
    <g role="img" aria-label="Night river with dark trees reflecting on shimmering water">
      <rect x="0" y="0" width="950" height="820" fill="url(#river-night)"/>
      <ellipse cx="420" cy="420" rx="330" ry="180" fill="url(#tree-glow)"/>
      <ellipse cx="300" cy="640" rx="300" ry="90" fill="url(#water-shimmer)"/>
    </g>

    <!-- ember bands -->
    <rect x="0" y="0" width="46" height="820" fill="url(#ember-left)"/>
    <rect x="46" y="0" width="70" height="820" fill="var(--navy-deep)" opacity="0.55"/>
    <path d="M230 0 H950 V40 C800 30 560 60 420 30 C340 20 280 40 230 30 Z" fill="var(--ember)" opacity="0.8"/>
    <path d="M0 420 L60 440 L40 760 L0 770 Z" fill="var(--ember)" opacity="0.55"/>
    <path d="M560 200 C700 150 860 120 950 110 V820 H720 C760 600 700 400 560 200 Z" fill="url(#ember-right)"/>
    <g stroke="var(--ember-dark)" stroke-width="3" opacity="0.45">
      <line x1="620" y1="140" x2="950" y2="60"/>
      <line x1="700" y1="230" x2="950" y2="170"/>
      <line x1="260" y1="140" x2="520" y2="60"/>
      <line x1="160" y1="600" x2="520" y2="520"/>
      <line x1="0" y1="330" x2="110" y2="300"/>
    </g>

    <!-- lagoon band -->
    <path d="M0 805 C250 735 520 710 950 705 V1200 H0 Z" fill="url(#lagoon)"/>
    <path d="M0 805 C250 735 520 710 950 705" fill="none" stroke="var(--pale)" stroke-width="9" opacity="0.9"/>
    <rect x="0" y="820" width="46" height="380" fill="var(--pale)" opacity="0.7"/>
    <rect x="46" y="820" width="22" height="380" fill="var(--cyan-deep)" opacity="0.6"/>
    <g stroke="var(--pale)" stroke-width="2" opacity="0.45">
      <line x1="230" y1="1010" x2="420" y2="1080"/>
      <line x1="90" y1="1150" x2="300" y2="1190"/>
      <line x1="500" y1="1165" x2="640" y2="1195"/>
    </g>

    <!-- taproom taps -->
    <rect role="img" aria-label="Blurred brewery taps behind the bar" x="620" y="780" width="330" height="420" fill="url(#taproom-glow)"/>

    <!-- pint photo area -->
    <rect role="img" aria-label="Photo of a pint glass of dark oatmeal stout with a creamy head" x="517" y="222" width="342" height="578" rx="28" fill="url(#pint-tones)"/>
  </svg>

  <svg class="headline" width="950" height="140" viewBox="0 0 950 140" xmlns="http://www.w3.org/2000/svg">
    <text x="78" y="134" textLength="784" lengthAdjust="spacingAndGlyphs" font-family="Righteous, Jost, sans-serif" font-size="84" fill="var(--title-grey)">COPPER &amp; FINCH BREWERY</text>
  </svg>

  <p class="tagline">Premium Craft Beer</p>

  <ul class="tasting-notes">
    <li>nice Stout</li>
    <li>clean flavor</li>
    <li>not to Heavy</li>
    <li>notes of Cinnamon Oatmeal</li>
    <li>tart and bitter</li>
    <li>aromatic, heavy Creamy finish</li>
    <li>hints of Cocoa</li>
  </ul>

  <div class="brand-seal">
    <span class="brand-seal-name">Copper<br>&amp; Finch</span>
  </div>

  <svg class="beer-name" width="950" height="90" viewBox="0 0 950 90" xmlns="http://www.w3.org/2000/svg">
    <text x="153" y="78" textLength="612" lengthAdjust="spacingAndGlyphs" font-family="Righteous, Jost, sans-serif" font-size="86" fill="var(--ink)">Pine Hollow Ember</text>
  </svg>

  <p class="beer-style">Oatmeal Stout</p>

  <p class="invite invite-lead">COME ENJOY SOME</p>
  <p class="invite invite-main">Cold Craft Beer and Wings</p>

  <p class="address">418 Lark Street, Port Huron MI</p>

</main>
</body>
</html>
```